Coastal Learner Bureau business cards

Australian company about to start offering its services. We recruit international students to come to study English, vocational education and postgraduate courses in Australia. We help them find the institution and select the right city they want to come to Australia. We are a young, online oriented and supportive agency. Our clients are between 18 and 35 years old, mainly University students, young professionals or people with work experience. We provide much more information that any other agency offer. We administrate a Facebook group with more than 11.000 members that daily ask questions about general information when coming to Australia, while they are here and even after they leave the country

Target Market(s)

International students from South America, Central America and Europe

Industry/Entity Type

Student

Contact Information for Business Card

Tomas Bilbrea
Managing Director
tomas@kelvarin.com.au
www.kelvoria.com.au
+61 491058264
Melbourne, Australia

Font styles to use
Serif
Sans Serif

Colors

Designer to choose colors to be used in the design.

Requirements
Must have
• Horizontal design
• Standard business card size and shape. If font uses green or yellow colours, they will have to match the ones from the logo
Nice to have
• UPDATE: Use the contents of the green image to design one of the card sides. Use our logo in the background of that side as watermark.
• Passport image, or immigration stamps. A picture of the Yarra River (from Melbourne) would be cool as well.
Should not have
• Non-standard business card size and shape
• Not black as the background colour of any sides as we are not a VIP agency or a hight class service. We are orientes to young people and they like colours, pictures, something attractive.
• Vertical design
• NO YELLOW or BLACK AS THE BACKGROUND COLOUR OF ANY SIDE OF THE BIZ CARD

```html
<!DOCTYPE html>
<html lang="en">
<head>
<meta charset="utf-8">
<title>Coastal Learner Bureau business cards</title>
<link rel="stylesheet" href="https://fonts.googleapis.com/css2?family=Open+Sans:wght@400;600;700;800&family=Chewy&display=swap">
<style>
  :root {
    --green: #04643c;
    --green-deep: #035232;
    --green-map: #0a7048;
    --gold: #e6b822;
    --gold-line: #eed9a0;
    --white: #ffffff;
    --ink: #1f1f1f;
    --stage: #e9ece9;
  }
  * { margin: 0; padding: 0; box-sizing: border-box; }
  html, body { width: 1200px; height: 900px; overflow: hidden; }
  body {
    background: var(--stage);
    font-family: "Open Sans", Arial, sans-serif;
    position: relative;
  }
  .card {
    position: absolute;
    left: 300px;
    width: 600px;
    height: 343px;
    overflow: hidden;
    box-shadow: 0 6px 18px rgba(0,0,0,0.18);
  }
  .card--back { top: 85px; background: var(--green); }
  .card--front { top: 472px; background: var(--white); }

  /* back side */
  .back__map {
    position: absolute; inset: 0;
    background: radial-gradient(ellipse at 55% 40%, var(--green-map) 0%, var(--green) 60%, var(--green-deep) 100%);
  }
  .back__brand {
    position: absolute; left: 0; right: 0; top: 120px;
    text-align: center;
    font-weight: 800; font-size: 54px; letter-spacing: 0.5px;
    color: var(--gold);
  }
  .back__web {
    position: absolute; left: 0; right: 0; bottom: 34px;
    text-align: center;
    font-size: 17px; letter-spacing: 0.6px;
    color: var(--white);
  }

  /* front side */
  .front__brand {
    position: absolute; left: 40px; top: 58px;
    font-weight: 800; font-size: 46px;
    color: var(--green);
  }
  .front__person {
    position: absolute; right: 34px; top: 70px; text-align: right;
    font-size: 14px; line-height: 1.25; color: var(--ink);
  }
  .front__name { font-weight: 700; color: var(--green); }
  .front__name span { color: var(--gold); }
  .front__rule {
    position: absolute; left: 40px; right: 34px; top: 118px;
    height: 1px; background: var(--gold-line);
  }
  .front__tagline {
    position: absolute; left: 40px; top: 176px;
    font-family: "Chewy", "Comic Sans MS", cursive;
    font-size: 26px; color: var(--green); letter-spacing: 0.5px;
  }
  .front__contacts {
    position: absolute; left: 40px; top: 216px;
    list-style: none; font-size: 15px; color: var(--ink);
  }
  .front__contacts li { display: flex; align-items: center; gap: 8px; height: 22px; }
  .contact-icon { width: 16px; height: 16px; flex: none; }
  .front__bands { position: absolute; left: 0; bottom: 0; width: 600px; height: 82px; }
  .front__city {
    position: absolute; right: 14px; bottom: 46px;
    font-size: 14px; color: var(--ink);
  }
</style>
</head>
<body>

<section class="card card--back" aria-label="Card back">
  <div class="back__map" role="img" aria-label="Faint world map in deep green tones"></div>
  <div class="back__brand">Kelvoria</div>
  <div class="back__web">www.kelvoria.com.au</div>
</section>

<section class="card card--front" aria-label="Card front">
  <div class="front__brand">Kelvoria</div>

  <div class="front__person">
    <div class="front__name">Tomas <span>Bilbrea</span></div>
    <div class="front__title">Managing Director</div>
  </div>
  <div class="front__rule"></div>

  <div class="front__tagline">Hacemos más por ti!</div>

  <ul class="front__contacts">
    <li>
      <svg class="contact-icon" viewBox="0 0 16 16" aria-hidden="true">
        <circle cx="8" cy="8" r="8" fill="var(--gold)"/>
        <path d="M5.2 4.2l1.5-.3.8 2-1 .8a5 5 0 0 0 2.8 2.8l.8-1 2 .8-.3 1.5c-3.6.2-6.8-3-6.6-6.6z" fill="var(--green)"/>
      </svg>
      +61 491058264
    </li>
    <li>
      <svg class="contact-icon" viewBox="0 0 16 16" aria-hidden="true">
        <circle cx="8" cy="8" r="8" fill="var(--gold)"/>
        <rect x="4" y="5.3" width="8" height="5.4" fill="none" stroke="var(--green)" stroke-width="1.2"/>
        <path d="M4 5.5l4 3 4-3" fill="none" stroke="var(--green)" stroke-width="1.2"/>
      </svg>
      tomas@kelvarin.com.au
    </li>
    <li>
      <svg class="contact-icon" viewBox="0 0 16 16" aria-hidden="true">
        <circle cx="8" cy="8" r="8" fill="var(--gold)"/>
        <circle cx="8" cy="8" r="4" fill="none" stroke="var(--green)" stroke-width="1.1"/>
        <path d="M4 8h8M8 4c-2 2.4-2 5.6 0 8M8 4c2 2.4 2 5.6 0 8" fill="none" stroke="var(--green)" stroke-width="1"/>
      </svg>
      www.kelvoria.com.au
    </li>
  </ul>

  <svg class="front__bands" viewBox="0 0 600 82" aria-hidden="true">
    <polygon points="0,42 300,42 330,0 430,0 430,82 0,82" fill="var(--green)"/>
    <polygon points="438,0 600,0 600,42 432,42" fill="var(--gold)"/>
    <rect x="430" y="42" width="170" height="40" fill="var(--green)"/>
  </svg>
  <div class="front__city">Melbourne, Australia</div>
</section>

</body>
</html>
```